Tallyo Scorecard

Redesign KTR's existing Tallyo scorecard, which tracks and reports key performance indicators (KPIs) for our clients. The scorecard provides our customers with an at-a-glance view of our on-site performance. Tallyo is a tool that automatically populates and reports this data.

Review the attached document and deliver suggested redesign options for the two attached views.
Page 1: Portfolio-wide views (high level rollup of multiple sites)
Page 2: Site-level view
Updates

Project Deadline Extended
Reason: Due to the holiday season within the U.S. around the globe we have decided to extend out deadline in hopes of gaining more participation. We will also be providing comments to the current designs tomorrow.

Font styles to use
Sans Serif

Requirements
Must have
• - Sans serif fonts
- Clean aesthetic
- Utilize the exact key performance indicators as are in the attached mockup
- White background (think Plover-esque)
Nice to have
• - Ideas for animation of design elements
Should not have
• - Pictures (icons are okay)

```html
<!DOCTYPE html>
<html lang="en">
<head>
<meta charset="UTF-8">
<title>Scorecard – KPI Score Details</title>
<link rel="stylesheet" href="https://fonts.googleapis.com/css2?family=Lato:ital,wght@0,300;0,400;0,700;1,300;1,400;1,700&display=swap">
<style>
  :root {
    --plum: #7e4a68;
    --ink: #7a7a7a;
    --ink-soft: #9a9a9a;
    --logo-grey: #c4c4c4;
    --track: #e6e6e6;
    --rule: #b5b5b5;
    --button: #eeeeee;
    --paper: #ffffff;
  }
  * { margin: 0; padding: 0; box-sizing: border-box; }
  html, body { width: 1200px; height: 675px; overflow: hidden; background: var(--paper); }
  body { font-family: "Lato", Arial, sans-serif; color: var(--ink); position: relative; }

  .logo-slot {
    position: absolute; font-style: italic; font-weight: 300;
    font-size: 26px; color: var(--logo-grey); white-space: nowrap;
  }
  .logo-slot--left { left: 142px; top: 27px; }
  .logo-slot--right { left: 1014px; top: 25px; }

  .main-nav {
    position: absolute; left: 2px; top: 88px; width: 1198px; height: 47px;
    background: var(--paper); box-shadow: 0 1px 5px rgba(0,0,0,.22);
  }
  .main-nav__item {
    position: absolute; top: 4px; height: 38px; line-height: 38px;
    font-weight: 300; font-size: 21px; color: var(--plum);
    transform: translateX(-50%); white-space: nowrap;
  }
  .main-nav__item--active {
    background: var(--plum); color: var(--paper);
    width: 170px; text-align: center;
  }

  .page-title {
    position: absolute; left: 54px; top: 178px;
    font-size: 30px; line-height: 33px; font-style: italic;
  }
  .page-title__section { display: block; font-weight: 700; color: var(--plum); }
  .page-title__name { display: block; font-weight: 700; color: var(--ink); }
  .page-title__period { display: block; font-weight: 300; color: var(--ink); }

  .site-score__label {
    position: absolute; left: 878px; top: 203px; font-style: italic; font-weight: 300;
    font-size: 18px; line-height: 23px; color: var(--ink-soft); white-space: nowrap;
  }
  .site-score__chart { position: absolute; left: 984px; top: 169px; }

  .kpi-head {
    position: absolute; top: 331px; font-size: 17px; font-weight: 400;
    color: var(--plum); white-space: nowrap;
  }
  .kpi-rule { position: absolute; left: 32px; top: 361px; width: 1110px; height: 1px; background: var(--rule); }
  .cell {
    position: absolute; font-size: 17px; font-weight: 300; color: var(--ink);
    white-space: nowrap; line-height: 21px;
  }
  .center { transform: translateX(-50%); }
  .points-bar { position: absolute; left: 819px; width: 292px; height: 19px; background: var(--track); }
  .points-bar__fill { height: 100%; background: var(--plum); }

  .expand-link {
    position: absolute; left: 1067px; top: 641px; width: 126px; height: 25px;
    background: var(--button); color: var(--plum); font-weight: 300; font-size: 20px;
    line-height: 26px; text-align: center; white-space: nowrap;
  }
</style>
</head>
<body>
  <div class="logo-slot logo-slot--left">Logo Here</div>
  <div class="logo-slot logo-slot--right">Logo Here</div>

  <nav class="main-nav">
    <span class="main-nav__item main-nav__item--active" style="left:93px">Governance</span>
    <span class="main-nav__item" style="left:251px">Cost</span>
    <span class="main-nav__item" style="left:394px">Quality</span>
    <span class="main-nav__item" style="left:543px">EHS</span>
    <span class="main-nav__item" style="left:683px">Personnel</span>
    <span class="main-nav__item" style="left:829px">Scorecard</span>
    <span class="main-nav__item" style="left:973px">Innovations</span>
    <span class="main-nav__item" style="left:1122px">Updates</span>
  </nav>

  <h1 class="page-title">
    <span class="page-title__section">Scorecard</span>
    <span class="page-title__name">KPI Score Details</span>
    <span class="page-title__period">July 2013</span>
  </h1>

  <div class="site-score__label">Site Score<br>Gole is 90%</div>
  <svg class="site-score__chart" width="134" height="134" viewBox="984 169 134 134">
    <circle cx="1050" cy="235" r="66" fill="var(--plum)"/>
    <path d="M1050 235 L1089.7 182.3 A66 66 0 0 1 1115.8 230.4 Z" fill="var(--track)"/>
    <text x="1053" y="277" text-anchor="middle" font-family="Lato, sans-serif" font-style="italic" font-weight="300" font-size="32" fill="#fff">86%</text>
  </svg>

  <section class="kpi-table">
    <div class="kpi-head" style="left:83px">Key Performance Indicators</div>
    <div class="kpi-head center" style="left:394px">KPI Score</div>
    <div class="kpi-head" style="left:503px">Target</div>
    <div class="kpi-head center" style="left:872px">Scored Points</div>
    <div class="kpi-head center" style="left:1045px">Possible Points</div>
    <div class="kpi-rule"></div>

    <div class="cell" style="left:83px;top:393px">Lorem Ipsum</div>
    <div class="cell center" style="left:395px;top:393px">4.0</div>
    <div class="cell" style="left:503px;top:393px">Less than control limit of 4<br>complaints per month</div>
    <div class="cell center" style="left:881px;top:393px">03</div>
    <div class="cell center" style="left:1049px;top:393px">05</div>
    <div class="points-bar" style="top:415px"><div class="points-bar__fill" style="width:182px"></div></div>

    <div class="cell" style="left:83px;top:485px">Dolor Sit Amet</div>
    <div class="cell center" style="left:395px;top:485px">3.2</div>
    <div class="cell" style="left:503px;top:485px">Lorem ipsum dolor sit amet</div>
    <div class="cell center" style="left:881px;top:485px">09</div>
    <div class="cell center" style="left:1049px;top:485px">10</div>
    <div class="points-bar" style="top:507px"><div class="points-bar__fill" style="width:263px"></div></div>

    <div class="cell" style="left:83px;top:577px">Lorem Ipsum</div>
    <div class="cell center" style="left:395px;top:577px">4.0</div>
    <div class="cell" style="left:503px;top:577px">Less than control limit of 4<br>complaints per month</div>
    <div class="cell center" style="left:881px;top:577px">03</div>
    <div class="cell center" style="left:1049px;top:577px">05</div>
    <div class="points-bar" style="top:599px"><div class="points-bar__fill" style="width:182px"></div></div>
  </section>

  <div class="expand-link">Exapand &gt;&gt;</div>
</body>
</html>
```